Construction business card

I need a new business card, they can connect with my logo, brand.
What we do is residential house , design and build
I like: Navy blue / black
I attached our logo, brand,
and, some idea for business card.

```html
<!DOCTYPE html>
<html lang="en">
<head>
<meta charset="utf-8">
<title>Talmore Building Group – Business Card</title>
<link rel="stylesheet" href="https://fonts.googleapis.com/css2?family=Poppins:wght@400;500;700&display=swap">
<style>
  :root {
    --stage: #2b2c2e;
    --card-black: #080607;
    --card-blue: #3580ca;
    --brand-blue: #3a86d6;
    --emboss-blue: #2f76bd;
    --white: #ffffff;
  }
  * { box-sizing: border-box; margin: 0; padding: 0; }
  html, body { width: 1200px; height: 939px; overflow: hidden; }
  body {
    background: var(--stage);
    font-family: "Poppins", sans-serif;
    position: relative;
  }
  .card {
    position: absolute;
    width: 560px;
    height: 320px;
    border-radius: 2px;
    box-shadow: 0 14px 30px rgba(0,0,0,.45);
    overflow: hidden;
  }
  /* Front */
  .card--front {
    left: 90px; top: 90px;
    background: var(--card-black);
    display: flex; flex-direction: column;
    align-items: center; justify-content: center;
    gap: 14px;
  }
  .brand {
    display: flex; align-items: center; gap: 14px;
  }
  .brand__square {
    width: 26px; height: 26px; background: var(--brand-blue);
  }
  .brand__name {
    color: var(--white);
    font-weight: 700;
    font-size: 30px;
    letter-spacing: 1px;
    line-height: 1.1;
  }
  .tagline {
    color: var(--white);
    font-weight: 700;
    font-size: 20px;
    letter-spacing: 3px;
  }
  .rule {
    width: 300px; height: 3px; background: var(--brand-blue);
  }
  /* Back */
  .card--back {
    left: 550px; top: 520px;
    background: var(--card-blue);
    color: var(--white);
  }
  .emboss-name {
    position: absolute;
    right: 28px; top: 46px;
    color: var(--emboss-blue);
    font-weight: 700;
    font-size: 26px;
    text-align: right;
    line-height: 1.15;
  }
  .contact {
    position: absolute;
    left: 34px; bottom: 34px;
  }
  .contact__name {
    font-weight: 700; font-size: 22px; letter-spacing: .5px;
  }
  .contact__role { font-size: 14px; margin-bottom: 6px; }
  .contact__line { font-size: 11.5px; line-height: 1.6; }
  .contact__list { list-style: none; margin-top: 4px; }
  .contact__list li {
    display: flex; align-items: center; gap: 8px;
    font-size: 12.5px; line-height: 1.75;
  }
  .icon { width: 13px; height: 13px; flex: none; }
</style>
</head>
<body>
  <section class="card card--front" aria-label="Business card front">
    <div class="brand">
      <span class="brand__square"></span>
      <span class="brand__name">TALMORE BUILDING GROUP</span>
    </div>
    <div class="rule"></div>
    <p class="tagline">DESIGN &amp; BUILD</p>
  </section>

  <section class="card card--back" aria-label="Business card back">
    <p class="emboss-name">TALMORE<br>BUILDING GROUP</p>
    <div class="contact">
      <p class="contact__name">MINH QUOC LAM</p>
      <p class="contact__role">Director</p>
      <p class="contact__line">TALMORE BUILDING GROUP PTY LTD</p>
      <p class="contact__line">ABN: 48 302 915 667</p>
      <ul class="contact__list">
        <li>
          <svg class="icon" viewBox="0 0 14 14"><rect x="3.5" y="1" width="7" height="12" rx="1.2" fill="none" stroke="#fff" stroke-width="1.4"/><rect x="5" y="2.8" width="4" height="6.5" fill="#fff"/></svg>
          0400 555 318
        </li>
        <li>
          <svg class="icon" viewBox="0 0 14 14"><rect x="1" y="3" width="12" height="8" fill="#fff"/><path d="M1 3 L7 8 L13 3" fill="none" stroke="#3580ca" stroke-width="1.3"/></svg>
          info@talmorebuilding.com.au
        </li>
        <li>
          <svg class="icon" viewBox="0 0 14 14"><path d="M7 13 C3 8 2.5 6.5 2.5 5 A4.5 4.5 0 0 1 11.5 5 C11.5 6.5 11 8 7 13Z" fill="#fff"/><circle cx="7" cy="5" r="1.7" fill="#3580ca"/></svg>
          22 Fernhill Rd, Ashgrove Park, VIC 3000
        </li>
        <li>
          <svg class="icon" viewBox="0 0 14 14"><circle cx="7" cy="7" r="5.8" fill="none" stroke="#fff" stroke-width="1.2"/><ellipse cx="7" cy="7" rx="2.5" ry="5.8" fill="none" stroke="#fff" stroke-width="1"/><path d="M1.2 7 H12.8 M2 4.3 H12 M2 9.7 H12" stroke="#fff" stroke-width="1"/></svg>
          www.talmorebuilding.com.au
        </li>
      </ul>
    </div>
  </section>
</body>
</html>
```